Compnay PowerPoint Tempalte Design

I am needing a good base design and slide designs for interior and exterior company presentations. The template will need to be on the company brand with proper coloring and fonts. Able to be creative with layout options with a good example attached.
website for reference: www.crewvlt.com/

Target Market(s)

Professionals

Font styles to use
Other font styles liked:
• Helvetica

Requirements
Must have
• On Brand Colors, Clean, simple design

```html
<!DOCTYPE html>
<html lang="en">
<head>
<meta charset="utf-8">
<title>VLT Company Presentation Template</title>
<link rel="stylesheet" href="https://fonts.googleapis.com/css2?family=Montserrat:wght@400;500;600;700;800&display=swap">
<style>
:root{
  --canvas:#6d6e70;
  --teal:#1f5a54;
  --blue:#0578a1;
  --aqua:#3c9c96;
  --ink:#231f20;
  --muted:#6a6a6a;
  --white:#ffffff;
  --dot:#dfe9ea;
}
*{margin:0;padding:0;box-sizing:border-box}
html,body{width:1200px;height:3482px;overflow:hidden}
body{background:var(--canvas);font-family:"Montserrat",Helvetica,Arial,sans-serif;color:var(--ink);position:relative}
.slide{position:absolute;left:99px;width:1001px;height:562px;background:var(--white);overflow:hidden}
.slide svg.layer{position:absolute;inset:0;width:100%;height:100%}
.footer-band{position:absolute;left:0;bottom:0;width:215px;height:56px}
.social{position:absolute;left:24px;bottom:16px;display:flex;gap:9px}
.social span{width:21px;height:21px;border-radius:50%;background:var(--dot)}
.page-num{position:absolute;right:0;bottom:0;width:90px;height:56px}
.page-num b{position:absolute;right:26px;bottom:8px;color:var(--white);font-size:28px;font-weight:700}

/* slide 1 */
.hero{top:108px}
.brand{position:absolute;left:44px;top:22px;display:flex;align-items:center;gap:10px}
.brand i{width:22px;height:22px;background:var(--aqua)}
.brand span{font-size:40px;font-weight:700;color:var(--ink);letter-spacing:-1px}
.hero h1{position:absolute;left:46px;top:175px;font-size:31px;line-height:42px;font-weight:700;color:var(--ink);letter-spacing:.3px}
.hero p{position:absolute;left:47px;top:310px;width:345px;font-size:13.5px;line-height:23.5px;font-weight:600}

/* slide 2 */
.about{top:784px}
.about-head{position:absolute;left:0;top:0;width:100%;height:104px;background:var(--blue);color:var(--white);text-align:center;font-size:36px;font-weight:700;line-height:104px;letter-spacing:.5px}
.about p{position:absolute;left:558px;top:228px;width:380px;font-size:12.5px;line-height:23.5px;font-weight:600}

/* slide 3 */
.services{top:1459px}
.tri-label{position:absolute;color:var(--white);font-size:16px;font-weight:700}
.services h2{position:absolute;left:0;width:100%;top:496px;text-align:center;font-size:38px;font-weight:800;color:var(--ink);letter-spacing:.5px}

/* slide 4 & 5 */
.values{top:2135px}
.team{top:2810px}
.section-head{position:absolute;left:0;top:0;width:370px;height:79px}
.section-head h2{position:absolute;left:42px;top:22px;color:var(--white);font-size:27px;font-weight:700;letter-spacing:.3px}
.team .section-head h2{left:61px}
.section-intro{position:absolute;right:24px;top:18px;width:590px;text-align:right;font-size:13.5px;line-height:23.5px;font-weight:600}
.value{position:absolute;top:375px;width:200px;text-align:center}
.value h3{font-size:16px;font-weight:600;letter-spacing:.3px}
.value p{margin-top:6px;font-size:11px;line-height:18px;color:var(--muted)}
.member{position:absolute;top:257px;width:250px}
.member h3{font-size:13px;line-height:23px;font-weight:600}
.member p{margin-top:10px;font-size:8.5px;line-height:13px;color:var(--muted)}
</style>
</head>
<body>

<!-- Slide 1: cover -->
<section class="slide hero">
  <svg class="layer" viewBox="0 0 1001 562">
    <defs>
      <linearGradient id="heroPhoto" x1="0" y1="0" x2="1" y2="1">
        <stop offset="0" stop-color="#d9d4cc"/><stop offset=".5" stop-color="#e89a35"/><stop offset="1" stop-color="#8c7a6a"/>
      </linearGradient>
    </defs>
    <polygon points="463,0 535,0 444,125 372,125" fill="var(--teal)"/>
    <polygon points="551,0 561,0 421,380 471,562 461,562 411,380" fill="var(--blue)"/>
    <polygon points="382,440 418,440 466,562 430,562" fill="var(--teal)"/>
    <g role="img" aria-label="Smiling team member in orange sweater in front of colleagues">
      <polygon points="573,0 990,0 1001,10 1001,562 493,562 440,380" fill="url(#heroPhoto)"/>
    </g>
    <polygon points="915,0 1001,0 1001,0 905,0" fill="var(--white)"/>
    <polygon points="960,0 1001,0 1001,90" fill="var(--white)"/>
    <polygon points="880,330 920,330 890,414 920,445 880,445 850,414" fill="var(--blue)"/>
    <polygon points="0,506 170,506 215,562 0,562" fill="var(--teal)"/>
    <polygon points="940,506 1001,506 1001,562 912,562" fill="var(--teal)"/>
    <polygon points="955,0 1001,0 1001,120" fill="var(--white)"/>
  </svg>
  <div class="brand"><i></i><span>VLT</span></div>
  <h1>WHERE WE MAINTAIN<br>A PASSION FOR<br>EXCELLENCE</h1>
  <p>Where we maintain a passion for excellence, striving to be better each and every day, so that our guests leave happy and our team members feel fulfilled.</p>
  <div class="social"><span></span><span></span><span></span><span></span><span></span></div>
  <div class="page-num"><b>1</b></div>
</section>

<!-- Slide 2: about -->
<section class="slide about">
  <svg class="layer" viewBox="0 0 1001 562">
    <defs>
      <linearGradient id="aboutPhoto" x1="0" y1="0" x2="1" y2="1">
        <stop offset="0" stop-color="#b8a48a"/><stop offset=".5" stop-color="#a87a4d"/><stop offset="1" stop-color="#3a4f6a"/>
      </linearGradient>
    </defs>
    <g role="img" aria-label="Team working together around a wooden table with notes and laptops">
      <polygon points="0,104 460,104 537,562 0,562" fill="url(#aboutPhoto)"/>
    </g>
    <polygon points="0,506 170,506 215,562 0,562" fill="var(--teal)"/>
    <polygon points="940,506 1001,506 1001,562 912,562" fill="var(--teal)"/>
    <polygon points="918,506 1001,506 1001,562 890,562" fill="var(--teal)"/>
  </svg>
  <div class="about-head">ABOUT US</div>
  <p>VLT is dedicated to cultivating a positive culture of leadership for its team members' professional and personal development, and this person-focused mentality transfers throughout the company from partners to our teams to guests. We strive to ensure each team member feels valued in all aspects of their role, reinforcing the importance of fostering a self-sustaining culture of success where everyone makes a team effort to communicate and overcome adversity.</p>
  <div class="social"><span></span><span></span><span></span><span></span><span></span></div>
  <div class="page-num"><b>2</b></div>
</section>

<!-- Slide 3: what we do -->
<section class="slide services">
  <svg class="layer" viewBox="0 0 1001 562">
    <defs>
      <linearGradient id="softBg" x1="0" y1="0" x2="1" y2="1">
        <stop offset="0" stop-color="#f4f6f7"/><stop offset="1" stop-color="#e6ebee"/>
      </linearGradient>
      <linearGradient id="estate" x1="0" y1="0" x2="0" y2="1">
        <stop offset="0" stop-color="#1f5a54"/><stop offset="1" stop-color="#2f4a45"/>
      </linearGradient>
      <linearGradient id="dining" x1="0" y1="0" x2="0" y2="1">
        <stop offset="0" stop-color="#15332f"/><stop offset="1" stop-color="#1f5a54"/>
      </linearGradient>
      <linearGradient id="office" x1="0" y1="0" x2="0" y2="1">
        <stop offset="0" stop-color="#0a4f6c"/><stop offset="1" stop-color="#0578a1"/>
      </linearGradient>
    </defs>
    <rect width="1001" height="562" fill="url(#softBg)" role="img" aria-label="Faded house model and documents background"/>
    <g role="img" aria-label="Residential house model">
      <polygon points="255,0 745,0 500,489" fill="url(#estate)"/>
    </g>
    <polygon points="255,54 61,435 453,435" fill="var(--blue)"/>
    <g role="img" aria-label="Restaurant dining room interior">
      <polygon points="255,66 72,428 453,428" fill="url(#dining)"/>
    </g>
    <polygon points="745,54 550,435 942,435" fill="var(--blue)"/>
    <g role="img" aria-label="Business colleagues meeting in an office">
      <polygon points="745,66 555,428 928,428" fill="url(#office)"/>
    </g>
    <polygon points="0,506 170,506 215,562 0,562" fill="var(--teal)"/>
    <polygon points="918,506 1001,506 1001,562 890,562" fill="var(--teal)"/>
  </svg>
  <span class="tri-label" style="left:455px;top:22px">Real Estate</span>
  <span class="tri-label" style="left:212px;top:381px">Restaurants</span>
  <span class="tri-label" style="left:685px;top:381px">Development</span>
  <h2>WHAT WE DO</h2>
  <div class="social"><span></span><span></span><span></span><span></span><span></span></div>
  <div class="page-num"><b>3</b></div>
</section>

<!-- Slide 4: core values -->
<section class="slide values">
  <svg class="layer" viewBox="0 0 1001 562">
    <rect width="1001" height="562" fill="url(#softBg)" role="img" aria-label="Faded house model background"/>
    <polygon points="0,0 370,0 327,79 0,79" fill="var(--blue)"/>
    <g transform="translate(168,258)">
      <polygon points="0,-100 100,0 0,100 -100,0" fill="var(--blue)"/>
      <g fill="var(--white)">
        <rect x="-42" y="-42" width="40" height="40" rx="6"/><rect x="2" y="-42" width="40" height="40" rx="6"/>
        <rect x="-42" y="2" width="40" height="40" rx="6"/><rect x="2" y="2" width="40" height="40" rx="6"/>
      </g>
    </g>
    <g transform="translate(385,258)">
      <polygon points="0,-100 100,0 0,100 -100,0" fill="var(--teal)"/>
      <g fill="var(--white)">
        <circle cx="0" cy="-30" r="11"/><path d="M-16 -12h32v20h-32z"/>
        <circle cx="-27" cy="-10" r="10"/><path d="M-42 6h30v34h-30z"/>
        <circle cx="27" cy="-10" r="10"/><path d="M12 6h30v34h-30z"/>
        <circle cx="0" cy="12" r="8"/><path d="M-11 24h22v16h-22z"/>
      </g>
    </g>
    <g transform="translate(602,258)">
      <polygon points="0,-100 100,0 0,100 -100,0" fill="var(--blue)"/>
      <g fill="var(--white)">
        <circle cx="0" cy="-16" r="20"/>
        <g transform="translate(0,-16)">
          <rect x="-5" y="-28" width="10" height="56"/><rect x="-28" y="-5" width="56" height="10"/>
          <rect x="-5" y="-28" width="10" height="56" transform="rotate(45)"/><rect x="-5" y="-28" width="10" height="56" transform="rotate(-45)"/>
        </g>
        <path d="M-40 0 l14 26 l0 18 h14 v-22 l-12 -22z"/><path d="M40 0 l-14 26 l0 18 h-14 v-22 l12 -22z"/>
      </g>
      <circle cx="0" cy="-16" r="8" fill="var(--blue)"/>
    </g>
    <g transform="translate(820,258)">
      <polygon points="0,-100 100,0 0,100 -100,0" fill="var(--teal)"/>
      <path d="M0 40 C-60 0 -45 -45 -20 -45 C-8 -45 0 -35 0 -30 C0 -35 8 -45 20 -45 C45 -45 60 0 0 40z" fill="var(--white)"/>
      <path d="M0 26 C-14 18 -14 4 -4 -6 C-4 4 4 2 6 -4 C14 8 12 20 0 26z" fill="var(--teal)"/>
    </g>
    <polygon points="0,506 170,506 215,562 0,562" fill="var(--teal)"/>
    <polygon points="918,506 1001,506 1001,562 890,562" fill="var(--teal)"/>
  </svg>
  <div class="section-head"><h2>OUR CORE VALUES</h2></div>
  <p class="section-intro">Our culture is founded on four core values and the entrepreneurial spirit of ownership that comes from a foundation of passion for our people, commitment to our business, transparency, and continued progress.</p>
  <div class="value" style="left:68px"><h3>INTEGRITY</h3><p>Integrity in everything we do. Do the right thing, even when no one is looking.</p></div>
  <div class="value" style="left:285px"><h3>FAMILY</h3><p>Family first, always. All decisions must benefit our family and the company.</p></div>
  <div class="value" style="left:502px"><h3>ESPECT</h3><p>We care for one another, praise efforts, recognize progress, and reward results.</p></div>
  <div class="value" style="left:720px"><h3>PASSION</h3><p>We are positive, hardworking, and disciplined in all we do, which stems from our innate passion.</p></div>
  <div class="social"><span></span><span></span><span></span><span></span><span></span></div>
  <div class="page-num"><b>4</b></div>
</section>

<!-- Slide 5: team -->
<section class="slide team">
  <svg class="layer" viewBox="0 0 1001 562">
    <rect width="1001" height="562" fill="url(#softBg)" role="img" aria-label="Faded house model background"/>
    <polygon points="0,0 370,0 327,79 0,79" fill="var(--blue)"/>
    <g>
      <polygon points="60,180 155,163 120,220" fill="var(--blue)"/>
      <circle cx="104" cy="205" r="38" fill="var(--teal)"/>
      <circle cx="104" cy="205" r="33" fill="#9fb3c0" role="img" aria-label="Portrait of Ryan Calder"/>
    </g>
    <g>
      <polygon points="377,180 472,163 437,220" fill="var(--blue)"/>
      <circle cx="421" cy="205" r="38" fill="var(--teal)"/>
      <circle cx="421" cy="205" r="33" fill="#c9a68a" role="img" aria-label="Portrait of Megan Thorpe"/>
    </g>
    <g>
      <polygon points="695,180 790,163 755,220" fill="var(--blue)"/>
      <circle cx="739" cy="205" r="38" fill="var(--teal)"/>
      <circle cx="739" cy="205" r="33" fill="#6f8fae" role="img" aria-label="Portrait of Evan Marsh"/>
    </g>
    <rect x="80" y="386" width="232" height="3" fill="var(--blue)"/>
    <polygon points="322,380 350,374 340,398" fill="var(--teal)"/>
    <rect x="360" y="386" width="270" height="3" fill="var(--blue)"/>
    <polygon points="640,380 668,374 658,398" fill="var(--teal)"/>
    <rect x="678" y="386" width="242" height="3" fill="var(--blue)"/>
    <polygon points="0,506 170,506 215,562 0,562" fill="var(--teal)"/>
    <polygon points="918,506 1001,506 1001,562 890,562" fill="var(--teal)"/>
  </svg>
  <div class="section-head"><h2>MEET THE TEAM</h2></div>
  <p class="section-intro">Together, we are creating a workplace culture consistent in quality and productivity to retain happy team members and rise to the challenge of establishing and maintaining guest-centered environments.</p>
  <div class="member" style="left:80px"><h3>RYAN CALDER<br>CEO</h3><p>Raised in Wichita, Kansas, Ryan has long felt a connection with the group that built the concept, enjoying the food, culture, and chance to be a part of this growing brand.</p></div>
  <div class="member" style="left:397px"><h3>MEGAN THORPE,<br>CONTROLLE</h3><p>Megan Thorpe is a seasoned veteran of the finance and accounting fields, using her experience to elevate VLT and its team members and guests. With years of careful counting under her belt.</p></div>
  <div class="member" style="left:714px"><h3>EVAN MARSH,<br>COO</h3><p>Seizing chances to change people's lives, in front of and behind the counter, Evan Marsh truly enjoys the people side of the food and service industries, a calling he found at nineteen.</p></div>
  <div class="social"><span></span><span></span><span></span><span></span><span></span></div>
  <div class="page-num"><b>5</b></div>
</section>

</body>
</html>
```